Maple n Brook - Contact/Landing Page

I need a landing page which will essentially be the page that customers will go to from the 'website' link on QTV listing. It will provide a short overview of services which need to be selectable. a little further down can capture some contact details followed by a large Submit Now button etc...

I have some icon/logo's that can be utilised at the bottom of the page as industry type references.

Target Market(s)

End of Lease Cleaning Services

Industry/Entity Type

Cleaning Service

Colors

Designer to choose colors to be used in the design.

Requirements
Must have
• As per description
Should not have
• Colours to match my website maplenbrook.com.au

```html
<!DOCTYPE html>
<html lang="en">
<head>
<meta charset="utf-8">
<title>Maple n Brook – End of Lease Services</title>
<link rel="stylesheet" href="https://fonts.googleapis.com/css2?family=Poppins:wght@400;500;600;700&family=Roboto:wght@400;500;700&display=swap">
<style>
  :root {
    --brand-blue: #1579bf;
    --brand-blue-deep: #1268ad;
    --button-blue: #3a7ac8;
    --card-grey: #e8e8e8;
    --footer-grey: #efefef;
    --ink: #222222;
    --muted: #666666;
    --accent-orange: #f9a000;
    --white: #ffffff;
  }
  * { box-sizing: border-box; margin: 0; padding: 0; }
  html, body { width: 1200px; height: 2427px; overflow: hidden; }
  body { position: relative; background: var(--white); font-family: "Roboto", sans-serif; color: var(--ink); }

  .hero { position: absolute; left: 0; top: 0; width: 1200px; height: 676px; background: var(--brand-blue); }
  .brand-mark { position: absolute; left: 0; top: 230px; width: 1200px; display: flex; justify-content: center; align-items: center; gap: 18px; }
  .brand-dot { width: 40px; height: 40px; border-radius: 50%; background: var(--white); }
  .brand-name { font-family: "Poppins", sans-serif; font-weight: 600; font-size: 52px; color: var(--white); }
  .hero-title { position: absolute; left: 0; top: 500px; width: 1200px; text-align: center; font-family: "Poppins", sans-serif; font-weight: 400; font-size: 43px; color: var(--white); }

  .service-card { position: absolute; top: 781px; width: 313px; height: 446px; background: var(--card-grey); text-align: center; }
  .service-card.is-active { border: 2px solid var(--brand-blue); box-shadow: 0 8px 14px rgba(0,0,0,0.25); width: 316px; top: 779px; height: 450px; }
  .service-photo { position: absolute; left: 9px; top: 9px; right: 9px; height: 187px; }
  .service-title { position: absolute; left: 0; right: 0; top: 219px; font-family: "Poppins", sans-serif; font-size: 21px; line-height: 26px; color: var(--ink); }
  .service-text { position: absolute; left: 24px; right: 24px; top: 284px; font-size: 13.5px; line-height: 26px; color: var(--muted); }
  .select-button { position: absolute; left: 51px; top: 373px; width: 211px; height: 46px; border-radius: 23px; background: var(--button-blue); color: var(--white); font-weight: 700; font-size: 13.5px; }
  .select-button span { position: absolute; left: 30px; top: 14px; }
  .select-button i { position: absolute; right: 2px; top: 2px; width: 42px; height: 42px; border-radius: 50%; background: var(--white); color: var(--button-blue); font-style: normal; font-size: 20px; line-height: 42px; text-align: center; }

  .contact-band { position: absolute; left: 0; top: 1321px; width: 1200px; height: 483px; background: linear-gradient(180deg, #1468ae 0%, #1675bd 55%, #166fb4 100%); }
  .contact-heading { position: absolute; left: 0; right: 0; top: 86px; text-align: center; font-family: "Poppins", sans-serif; font-size: 34px; color: var(--white); }
  .field { position: absolute; height: 46px; background: var(--white); font-size: 14px; color: #777; padding: 15px 16px; }
  .submit-button { position: absolute; left: 480px; top: 353px; width: 241px; height: 46px; background: var(--accent-orange); border: 2px solid var(--white); color: var(--white); font-weight: 700; font-size: 13.5px; text-align: center; line-height: 42px; }

  .partner { position: absolute; top: 1898px; width: 231px; height: 113px; background: var(--white); box-shadow: 0 2px 6px rgba(0,0,0,0.12); display: flex; align-items: center; justify-content: center; }
  .partner-badge { width: 180px; height: 60px; border-radius: 6px; }
  .carousel-arrow { position: absolute; top: 1938px; }

  .footer { position: absolute; left: 0; top: 2106px; width: 1200px; height: 321px; background: var(--footer-grey); font-family: "Poppins", sans-serif; }
  .footer-heading { position: absolute; top: 78px; font-weight: 700; font-size: 20px; color: #333; }
  .footer-blurb { position: absolute; left: 111px; top: 124px; width: 290px; font-size: 13.5px; line-height: 16.5px; color: #555; }
  .contact-line { position: absolute; left: 505px; display: flex; align-items: flex-start; gap: 8px; font-size: 13.5px; line-height: 16px; color: #555; }
  .contact-icon { width: 36px; height: 36px; border-radius: 50%; background: var(--button-blue); display: flex; align-items: center; justify-content: center; flex: none; }
  .pill { position: absolute; left: 894px; width: 165px; height: 48px; border-radius: 24px; text-align: center; line-height: 48px; font-weight: 600; font-size: 13.5px; }
  .pill-light { top: 66px; background: var(--white); color: #333; }
  .pill-blue { top: 127px; background: var(--button-blue); color: var(--white); }
  .copyright { position: absolute; left: 827px; top: 210px; font-size: 15px; line-height: 26px; color: #666; }
</style>
</head>
<body>

<header class="hero">
  <div class="brand-mark"><span class="brand-dot"></span><span class="brand-name">Maple n Brook</span></div>
  <h1 class="hero-title">End of Lease Services</h1>
</header>

<section class="services">
  <article class="service-card" style="left:111px;">
    <div class="service-photo" role="img" aria-label="Cleaner vacuuming a bright living room" style="background:linear-gradient(135deg,#e9e9e7,#c9c8c2 60%,#9aa29a);"></div>
    <h2 class="service-title" style="top:205px;">End of<br>Lease Cleaning</h2>
    <p class="service-text">All interior cleaning carried out as per your Property Management requirements.</p>
    <div class="select-button"><span>SELECT</span><i>+</i></div>
  </article>
  <article class="service-card is-active" style="left:442px;">
    <div class="service-photo" role="img" aria-label="Carpet steam cleaning wand on grey carpet" style="background:linear-gradient(180deg,#8a8470,#a5a7b0 45%,#8e93a3);"></div>
    <h2 class="service-title">Carpet Cleaning</h2>
    <p class="service-text">All your carpet steam cleaning needs carried out to meet the Australian Standards AS 3733 : 1995</p>
    <div class="select-button"><span>SELECT</span><i>+</i></div>
  </article>
  <article class="service-card" style="left:776px;">
    <div class="service-photo" role="img" aria-label="Technician in protective suit spraying a kitchen" style="background:linear-gradient(135deg,#f2f3f4,#dfe1e3 60%,#c3c6c8);"></div>
    <h2 class="service-title">Pest Control</h2>
    <p class="service-text">Flea Treatment carried out as per mandatory tenancy requirements for pets on premises.</p>
    <div class="select-button"><span>SELECT</span><i>+</i></div>
  </article>
</section>

<section class="contact-band">
  <h2 class="contact-heading">CONTACT US</h2>
  <div class="field" style="left:283px;top:156px;width:309px;">First name</div>
  <div class="field" style="left:609px;top:156px;width:309px;">Surname</div>
  <div class="field" style="left:283px;top:218px;width:309px;">Email address</div>
  <div class="field" style="left:609px;top:218px;width:309px;">Phone</div>
  <div class="field" style="left:283px;top:280px;width:635px;">Suburb</div>
  <div class="submit-button">SUBMIT NOW FOR YOUR QUOTE</div>
</section>

<section class="partners">
  <svg class="carousel-arrow" style="left:42px;" width="20" height="32" viewBox="0 0 20 32"><path d="M15 4 L5 16 L15 28" fill="none" stroke="#555" stroke-width="2.5"/></svg>
  <div class="partner" style="left:111px;"><div class="partner-badge" style="background:#1a1a1a;"></div></div>
  <div class="partner" style="left:360px;"><div class="partner-badge" style="background:#3b4e9c;height:40px;"></div></div>
  <div class="partner" style="left:609px;"><div class="partner-badge" style="background:#1f3e8f;width:140px;height:80px;"></div></div>
  <div class="partner" style="left:858px;background:#8db54a;"><div class="partner-badge" style="background:#a4c86a;"></div></div>
  <svg class="carousel-arrow" style="left:1132px;" width="20" height="32" viewBox="0 0 20 32"><path d="M5 4 L15 16 L5 28" fill="none" stroke="#555" stroke-width="2.5"/></svg>
</section>

<footer class="footer">
  <h3 class="footer-heading" style="left:111px;">READY TO GET STARTED?</h3>
  <p class="footer-blurb">Lorem ipsum dolor sit amet, consectetur adipiscing elit, sed do eiusmod tempor incididunt ut labore et dolore magna aliqua. Ut enim ad minim veniam, quis nostrud exercitation</p>

  <h3 class="footer-heading" style="left:505px;">CONTACT US</h3>
  <div class="contact-line" style="top:122px;">
    <span class="contact-icon"><svg width="12" height="16" viewBox="0 0 12 16"><path d="M6 0C2.7 0 0 2.6 0 5.8 0 10 6 16 6 16s6-6 6-10.2C12 2.6 9.3 0 6 0zm0 8a2.2 2.2 0 1 1 0-4.4A2.2 2.2 0 0 1 6 8z" fill="#fff"/></svg></span>
    <span style="padding-top:2px;">27 Wattle Crescent,<br>Riverton, 2790.</span>
  </div>
  <div class="contact-line" style="top:182px;">
    <span class="contact-icon"><svg width="14" height="14" viewBox="0 0 24 24"><path d="M6.6 10.8a15 15 0 0 0 6.6 6.6l2.2-2.2c.3-.3.7-.4 1-.2 1.1.4 2.3.6 3.6.6.6 0 1 .4 1 1V20c0 .6-.4 1-1 1A17 17 0 0 1 3 4c0-.6.4-1 1-1h3.5c.6 0 1 .4 1 1 0 1.3.2 2.5.6 3.6.1.3 0 .7-.2 1z" fill="#fff"/></svg></span>
    <span style="padding-top:2px;">0400 555 123</span>
  </div>
  <div class="contact-line" style="top:230px;">
    <span class="contact-icon"><svg width="14" height="11" viewBox="0 0 14 11"><rect width="14" height="11" rx="1" fill="#fff"/><path d="M0.5 1 L7 6 L13.5 1" fill="none" stroke="#3a7ac8" stroke-width="1.3"/></svg></span>
    <span style="padding-top:3px;">info@maplenbrook.com.au</span>
  </div>

  <div class="pill pill-light">GET IN TOUCH</div>
  <div class="pill pill-blue">OUR WORK</div>
  <p class="copyright">©&nbsp; Copyrights 2021 Company name |<br>All Rights Reserved</p>
</footer>

</body>
</html>
```